wealth management firm, professional group, new model

we have a logo that works but we need a card, white background using our colors...clean look

our tag line if can be used in

The Path from Saver to Steward

```html
<!DOCTYPE html>
<html lang="en">
<head>
<meta charset="utf-8">
<title>Varro Wealth Partners – Business Card</title>
<link href="https://fonts.googleapis.com/css2?family=Montserrat:ital,wght@0,400;0,500;1,400&display=swap" rel="stylesheet">
<style>
  :root {
    --backdrop: #262626;
    --navy: #14284a;
    --navy-deep: #12254a;
    --navy-light: #1a2f55;
    --paper: #f2f2f2;
    --paper-shade: #e3e3e3;
    --silver: #d7dbe2;
  }
  * { margin: 0; padding: 0; box-sizing: border-box; }
  html, body {
    width: 1200px; height: 576px; overflow: hidden;
    background: var(--backdrop);
    font-family: "Montserrat", sans-serif;
  }
  .canvas { position: relative; width: 1200px; height: 576px; }

  .card {
    position: absolute;
    border-radius: 10px;
  }

  /* Back side */
  .card-back {
    left: 102px; top: 138px; width: 484px; height: 294px;
    background: linear-gradient(180deg, var(--navy-light) 0%, var(--navy-deep) 100%);
  }
  .card-back .brand-name {
    position: absolute; left: 0; right: 0; top: 134px;
    text-align: center;
    color: var(--silver);
    font-size: 17px; font-weight: 500;
    letter-spacing: 4px; text-transform: uppercase;
  }
  .card-back .tagline {
    position: absolute; left: 0; right: 0; top: 248px;
    text-align: center;
    color: var(--silver);
    font-size: 13px; letter-spacing: 0.6px;
  }

  /* Front side */
  .card-front {
    left: 596px; top: 138px; width: 480px; height: 291px;
    background: linear-gradient(180deg, var(--paper) 0%, var(--paper-shade) 100%);
    color: var(--navy);
  }
  .holder { position: absolute; left: 22px; top: 44px; }
  .holder-name { font-size: 22px; font-weight: 400; line-height: 1.2; }
  .holder-title { font-size: 12.5px; font-weight: 500; margin-top: 1px; }

  .brand-lockup {
    position: absolute; right: 30px; top: 58px;
    font-size: 13px; font-weight: 500;
    letter-spacing: 3.5px; text-transform: uppercase;
  }

  .contacts { position: absolute; left: 22px; top: 178px; list-style: none; }
  .contacts li {
    display: flex; align-items: center; gap: 9px;
    font-size: 13px; font-weight: 500; height: 20px;
  }
  .contacts svg { width: 12px; height: 12px; fill: var(--navy); }

  .divider {
    position: absolute; left: 0; right: 0; top: 245px;
    height: 3px; background: var(--navy);
  }
  .card-front .tagline {
    position: absolute; left: 22px; top: 259px;
    font-size: 13px; font-style: italic; letter-spacing: 0.6px;
  }
</style>
</head>
<body>
<div class="canvas">

  <section class="card card-back">
    <p class="brand-name">Varro Wealth Partners</p>
    <p class="tagline">The Path from Saver to Steward</p>
  </section>

  <section class="card card-front">
    <div class="holder">
      <h1 class="holder-name">Mark Delano</h1>
      <p class="holder-title">Managing Director</p>
    </div>

    <p class="brand-lockup">Varro Wealth Partners</p>

    <ul class="contacts">
      <li>
        <svg viewBox="0 0 12 12" aria-hidden="true"><path d="M1 4 C1 2 3 1 6 1 C9 1 11 2 11 4 L8.5 4.5 L8 3.2 C7 2.9 5 2.9 4 3.2 L3.5 4.5 Z M3 6 L9 6 L10.5 11 L1.5 11 Z"/></svg>
        <span>555-201-4870</span>
      </li>
      <li>
        <svg viewBox="0 0 12 12" aria-hidden="true"><path d="M1 2.5 H11 V9.5 H1 Z M1.8 3.3 L6 6.5 L10.2 3.3 Z" fill-rule="evenodd"/></svg>
        <span>mark@varropartners.com</span>
      </li>
      <li>
        <svg viewBox="0 0 12 12" aria-hidden="true"><path d="M6 1 A5 5 0 1 0 6 11 A5 5 0 1 0 6 1 Z M6 2 C7 3 7.5 4.5 7.5 6 C7.5 7.5 7 9 6 10 C5 9 4.5 7.5 4.5 6 C4.5 4.5 5 3 6 2 Z M2 5.5 H10 V6.5 H2 Z" fill-rule="evenodd"/></svg>
        <span>www.varropartners.com</span>
      </li>
    </ul>

    <div class="divider"></div>
    <p class="tagline">The Path from Saver to Steward</p>
  </section>

</div>
</body>
</html>
```